Flyer / Small Safety "Poster" (A4 or 8.5x11" paper)

We're looking to create a series of safety signs for woodworkers to print on home printers using standard sized paper (A4 or 8.5x11" depending on where they are), or possibly to have printed on 17x22" paper.
Currently we want only the first one, but keep in mind that all should work together.
They need: Simple graphic. Bold Text. Company logo. Use company colors (orange, black, white.)
To begin, we will start with a single sign for hearing protection. Graphic or clip art to portray either ear plugs or ear-muff design. Text to say, "Hearing Protection is a Sound Investment."

Target Market(s)

USA Woodworkers & CNC Machinists - Male, 20-65 years old

Font styles to use
Sans Serif

Colors
f37122

Requirements
Must have
• Client logo
Nice to have
• Use client colors of black, white, & orange

```html
<!DOCTYPE html>
<html lang="en">
<head>
<meta charset="utf-8">
<title>Hearing Protection Safety Poster</title>
<link href="https://fonts.googleapis.com/css2?family=Anton&family=Montserrat:ital,wght@0,600;0,700;0,800;1,500&display=swap" rel="stylesheet">
<style>
  :root {
    --backdrop: #d9d9db;
    --orange-light: #e39a55;
    --orange: #c8782f;
    --orange-deep: #9a4f1a;
    --ink: #111111;
    --paper: #ffffff;
    --cup-dark: #4a3e45;
    --cup-gold: #f0c46e;
  }
  * { margin: 0; padding: 0; box-sizing: border-box; }
  html, body {
    width: 1130px;
    height: 1200px;
    overflow: hidden;
    background: var(--backdrop);
  }
  .canvas {
    position: relative;
    width: 1130px;
    height: 1200px;
    display: flex;
    align-items: center;
    justify-content: center;
  }
  .poster {
    position: relative;
    width: 820px;
    height: 1160px;
    overflow: hidden;
    background:
      radial-gradient(ellipse 60% 45% at 50% 52%, var(--orange-light) 0%, rgba(227,154,85,0) 100%),
      linear-gradient(135deg, var(--orange) 0%, #c47530 45%, var(--orange-deep) 100%);
  }
  .illustration {
    position: absolute;
    left: 32px;
    top: 117px;
    width: 753px;
    height: 710px;
    border-radius: 380px 380px 60px 60px;
    background: linear-gradient(180deg, rgba(74,62,69,0.35) 0%, rgba(240,196,110,0.25) 60%, rgba(74,62,69,0.35) 100%);
  }
  .headline {
    position: absolute;
    left: 0;
    right: 0;
    text-align: center;
  }
  .headline-hearing {
    top: 288px;
    font-family: "Anton", "Impact", sans-serif;
    font-size: 150px;
    line-height: 1;
    color: var(--paper);
    letter-spacing: 1px;
    transform: scaleX(0.95);
  }
  .headline-protection {
    top: 462px;
    font-family: "Anton", "Impact", sans-serif;
    font-size: 96px;
    line-height: 1;
    color: var(--ink);
  }
  .tagline-sound {
    top: 584px;
    font-family: "Montserrat", sans-serif;
    font-weight: 700;
    font-size: 56px;
    line-height: 1;
    color: var(--ink);
  }
  .tagline-investment {
    top: 650px;
    font-family: "Montserrat", sans-serif;
    font-weight: 700;
    font-size: 39px;
    line-height: 1;
    color: var(--paper);
  }
  .brand {
    position: absolute;
    left: 0;
    right: 0;
    top: 900px;
    display: flex;
    align-items: center;
    justify-content: center;
    gap: 14px;
  }
  .brand-square {
    width: 40px;
    height: 40px;
    background: var(--paper);
  }
  .brand-name {
    font-family: "Montserrat", sans-serif;
    font-weight: 800;
    font-size: 42px;
    letter-spacing: 3px;
    color: var(--paper);
  }
  .brand-slogan {
    position: absolute;
    left: 0;
    right: 0;
    top: 968px;
    text-align: center;
    font-family: "Montserrat", sans-serif;
    font-weight: 600;
    font-size: 16px;
    color: var(--paper);
  }
  .web-address {
    position: absolute;
    left: 0;
    right: 0;
    top: 1082px;
    text-align: center;
    font-family: "Montserrat", sans-serif;
    font-weight: 700;
    font-size: 33px;
    letter-spacing: 2px;
    color: var(--paper);
  }
</style>
</head>
<body>
  <main class="canvas">
    <article class="poster">
      <div class="illustration" role="img" aria-label="Illustration of yellow and dark grey safety ear-muffs with a headband arching over the headline"></div>
      <h1 class="headline headline-hearing">HEARING</h1>
      <p class="headline headline-protection">PROTECTION</p>
      <p class="headline tagline-sound">Is a Sound</p>
      <p class="headline tagline-investment">INVESTMENT</p>
      <div class="brand">
        <span class="brand-square"></span>
        <span class="brand-name">CUTLINE SUPPLY</span>
      </div>
      <p class="brand-slogan">Your source for industrial cutting tools!</p>
      <p class="web-address">www.cutlinesupply.com</p>
    </article>
  </main>
</body>
</html>
```